Bright Harbor Goods - Product Page

Looking for a design for our product pages to showcase all of the following information in an aesthetically pleasing way. <br/><br/>• Product price per piece & price breaks<br/>• Set up cost <br/>• Additional color cost<br/>• Imprint side <br/>• Product Dimensions<br/><br/>Attached are photos showing ideas we have come up with to display the information. <br/><br/>The link below shows how our product pages is currently laid out. <br/><br/>Link to webpage: https://www.brightharborgoods-example.com/non-woven-reusable-promo-totes.html<br/>

Number of Pages Required

1 page

Colors
33b8a4
33a6d7
3277b5
fece3e
f9a040
a3cd3a

Requirements
Must have
• • Product price per piece & price breaks
• • Set up cost
• • Additional color cost
• • Imprint side
• • Product Dimensions

```html
<!DOCTYPE html>
<html lang="en">
<head>
<meta charset="utf-8">
<title>Non-Woven Reusable Promo Totes | Bright Harbor Goods</title>
<link href="https://fonts.googleapis.com/css2?family=Fira+Sans:wght@400;500;600;700&family=Open+Sans:wght@400;600;700&display=swap" rel="stylesheet">
<style>
:root{
  --teal:#33b8a4;--sky:#33a6d7;--blue:#3277b5;--navy:#2a5fa0;
  --yellow:#fece3e;--orange:#f9a040;--lime:#a3cd3a;--green:#4aa83a;
  --ink:#222;--muted:#555;--gray:#f2f2f2;--gray2:#e9e9e9;--dark:#1c1c1c;
}
*{box-sizing:border-box;margin:0;padding:0}
html,body{width:1200px;height:3668px;overflow:hidden;background:#fff}
body{font-family:"Open Sans",Arial,sans-serif;color:var(--ink)}
.page{position:relative;width:1200px;height:3668px;overflow:hidden}
.abs{position:absolute}
.head{font-family:"Fira Sans",Arial,sans-serif}
svg.ico{display:inline-block;vertical-align:middle}

/* header */
.site-header{top:0;left:0;width:1200px;height:124px;background:#fff}
.brand{left:78px;top:30px;display:flex;align-items:center;gap:10px}
.brand-dot{width:26px;height:26px;border-radius:50%;background:var(--lime)}
.brand-name{font-family:"Fira Sans",sans-serif;font-weight:700;font-size:30px;color:var(--green);letter-spacing:-.3px}
.top-links{left:450px;top:55px;font-size:11px;font-weight:700;display:flex;gap:12px}
.top-links span.sep{font-weight:400}
.call{left:760px;top:42px;display:flex;align-items:center;gap:10px}
.round{width:34px;height:34px;border-radius:50%;background:#f0f0f0;display:flex;align-items:center;justify-content:center}
.call b{font-family:"Fira Sans",sans-serif;font-size:25px;font-weight:600}
.tools{left:990px;top:42px;display:flex;gap:16px}
.cart-count{position:absolute;right:-4px;top:-6px;font-size:10px}

.main-nav{top:124px;left:0;width:1200px;height:47px;background:linear-gradient(90deg,var(--teal),#32aecb 60%,var(--sky));display:flex;justify-content:center;align-items:center;gap:38px}
.main-nav a{color:#fff;font-family:"Fira Sans",sans-serif;font-weight:600;font-size:15px;text-decoration:none}

.crumbs{left:74px;top:200px;font-family:"Fira Sans",sans-serif;font-size:15px;font-weight:500;color:#444;display:flex;gap:18px}

/* product */
.product-band{top:253px;left:0;width:1200px;height:155px;background:var(--gray)}
.product-title{left:71px;top:265px;font-size:27px;font-weight:600;color:var(--orange)}
.photo-main{left:74px;top:326px;width:450px;height:436px;background:#fff;box-shadow:0 1px 6px rgba(0,0,0,.12)}
.photo-main .fill{position:absolute;left:110px;top:40px;width:240px;height:340px;background:linear-gradient(120deg,#d7262e 0 45%,#c9b48d 55% 100%);border-radius:4px}
.thumb{top:776px;width:100px;height:107px;background:#fff;box-shadow:0 1px 5px rgba(0,0,0,.15);display:flex;align-items:center;justify-content:center}
.thumb i{display:block;width:48px;height:62px;border-radius:3px}
.thumb.more{color:var(--blue);font-size:24px}

.sku{left:559px;top:344px;font-size:33px;font-weight:600;color:var(--blue)}
.rev-link{left:891px;top:334px;font-size:16px;color:#333}
.stars-lg{left:889px;top:362px;display:flex;gap:14px}
.spec-line{left:561px;font-size:19px;color:#333}
.stock-h{left:561px;font-size:27px;font-weight:600;color:var(--blue)}

.price-table{left:561px;width:565px;height:109px;display:grid;grid-template-columns:85px repeat(7,1fr);grid-template-rows:1fr 1fr;background:var(--gray);box-shadow:0 2px 4px rgba(0,0,0,.15)}
.price-table div{display:flex;align-items:center;justify-content:center;font-size:13px;color:var(--blue)}
.price-table .lab{background:var(--yellow);color:var(--ink);font-family:"Fira Sans",sans-serif;font-weight:600;font-size:19px}

.btn{top:915px;width:174px;height:46px;border-radius:23px;display:flex;align-items:center;justify-content:center;font-family:"Fira Sans",sans-serif;font-weight:600;font-size:15px}
.btn.quote{left:558px;background:var(--yellow)}
.btn.buy{left:739px;background:linear-gradient(90deg,var(--teal),var(--sky));color:#fff}
.btn.sample{left:920px;background:var(--lime)}

/* sample form */
.sample-form{top:1018px;left:0;width:1200px;height:306px;background:radial-gradient(ellipse at 50% 60%,#3a8fd0 0%,var(--blue) 55%,#2b68a8 100%)}
.sample-form h2{position:absolute;top:28px;width:100%;text-align:center;color:#fff;font-family:"Fira Sans",sans-serif;font-weight:600;font-size:24px}
.field{position:absolute;width:305px;height:35px;background:#fff;font-size:13px;color:#444;padding:0 13px;display:flex;align-items:center;justify-content:space-between}
.submit{position:absolute;left:514px;top:208px;width:172px;height:42px;border-radius:21px;background:var(--yellow);display:flex;align-items:center;justify-content:center;font-family:"Fira Sans",sans-serif;font-weight:600;font-size:14px}

/* tabs */
.tabs{top:1357px;left:290px;height:34px;display:flex;align-items:center;font-size:14px;font-weight:700;font-family:"Fira Sans",sans-serif}
.tabs .on{background:var(--teal);color:#fff;border-radius:17px;padding:0 24px;height:34px;display:flex;align-items:center}
.tabs .sep{margin:0 24px;font-weight:400}
.details-h{top:1420px;left:0;width:1200px;text-align:center;color:var(--teal);font-size:24px;font-weight:600}

.specs{left:117px;top:1470px;width:965px;display:grid;grid-template-columns:211px 1fr}
.specs dt,.specs dd{border-bottom:1px solid #fff;font-size:13px}
.specs dt{background:var(--gray2);font-family:"Fira Sans",sans-serif;font-weight:600;font-size:16px;padding-left:47px;height:66px;display:flex;align-items:center}
.specs dd{background:var(--gray);padding-left:36px;height:66px;display:flex;align-items:center}
.specs dt.tall{height:350px;align-items:flex-start;padding-top:23px}
.specs dd.tall{height:350px;align-items:flex-start;padding-top:28px}
.features{list-style:none}
.features li{height:33px;display:flex;align-items:center;gap:14px}
.features li::before{content:"›";font-weight:700;font-size:16px}

/* reviews */
.reviews{top:2278px;left:0;width:1200px;height:407px;background:var(--gray)}
.reviews h2{position:absolute;top:30px;width:100%;text-align:center;color:var(--teal);font-family:"Fira Sans",sans-serif;font-size:24px;font-weight:600}
.review{position:absolute;background:#fff;padding:30px 0 0 0}
.review .stars{display:flex;gap:15px}
.review p{font-size:15px;line-height:22px;color:#333;margin-top:18px}
.review .by{font-size:15px;margin-top:20px;color:#333}
.review .by b{font-family:"Fira Sans",sans-serif;font-size:19px;font-weight:600}
.more{color:var(--teal);font-weight:600}
.all-link{left:365px;top:2604px;font-family:"Fira Sans",sans-serif;font-weight:600;font-size:15px;color:var(--blue);text-decoration:underline}

/* recommended */
.rec-h{top:2755px;left:0;width:1200px;text-align:center;font-size:24px;font-weight:600}
.card{top:2821px;width:241px;height:360px;background:#fff;box-shadow:0 1px 6px rgba(0,0,0,.15);text-align:center}
.card .pic{height:192px;border-bottom:1px solid #eee;display:flex;align-items:center;justify-content:center}
.card .pic i{display:block;width:150px;height:130px;border-radius:4px}
.card .info{font-size:17px;line-height:22px;margin-top:24px}
.card .info b{font-weight:600}
.card .stars{display:flex;justify-content:center;gap:14px;margin-top:18px}
.card small{display:block;font-size:11px;margin-top:6px}

/* footer */
.site-footer{top:3227px;left:0;width:1200px;height:293px;background:linear-gradient(90deg,#2d62a6,var(--blue))}
.imprint-card{position:absolute;left:78px;top:29px;width:217px;height:182px;background:#fff;padding:6px;font-family:Arial,sans-serif;font-size:7.5px;color:#111}
.imprint-card .t{font-weight:700;font-size:9px;color:#334;padding-left:3px}
.imprint-card .box{border:1px solid #7ab;margin-top:3px}
.imprint-card .r1{background:#9fd3ef;text-align:center;padding:2px 0;font-weight:700;font-size:10px}
.imprint-card .r2{background:#9fd3ef;text-align:center;font-size:7px;padding-bottom:2px}
.imprint-card .r3{background:#ffe03a;text-align:center;font-size:9px;padding:3px 0}
.imprint-card .row{display:flex;justify-content:space-between;padding:2px 4px;border-top:1px solid #9bd}
.imprint-card .row.b{background:#9fd3ef}
.foot-brand{position:absolute;left:366px;top:34px;font-family:"Fira Sans",sans-serif;font-weight:700;font-size:30px;color:#fff}
.foot-about{position:absolute;left:370px;top:122px;width:250px;font-size:11.5px;line-height:22px;color:#fff}
.foot-col{position:absolute;top:50px;color:#fff}
.foot-col h3{font-family:"Fira Sans",sans-serif;font-size:16px;font-weight:600;margin-bottom:18px}
.foot-col ul{list-style:none;font-size:11.5px;line-height:22px}
.foot-col li::before{content:"›";margin-right:12px;font-weight:700}

.contact-band{top:3520px;left:0;width:1200px;height:103px;background:linear-gradient(90deg,var(--teal),#33afc8 55%,var(--sky));color:#fff}
.contact-band .addr{position:absolute;left:127px;top:28px;font-size:15px;line-height:21px}
.contact-band .ph{position:absolute;left:541px;top:34px;font-family:"Fira Sans",sans-serif;font-size:24px;font-weight:600}
.contact-band .em{position:absolute;left:911px;top:40px;font-size:15px}
.bottom-bar{top:3623px;left:0;width:1200px;height:45px;background:var(--dark);color:#fff;font-size:13px}
.bottom-bar .copy{position:absolute;left:78px;top:13px}
.social{position:absolute;left:928px;top:15px;display:flex;gap:29px}
.social i{display:block;width:14px;height:14px;border-radius:50%;background:#fff}
.bottom-bar .code{position:absolute;left:1152px;top:15px;font-size:11px}
</style>
</head>
<body>
<svg width="0" height="0" style="position:absolute">
  <symbol id="star" viewBox="0 0 24 24"><path d="M12 1.8l3.1 6.6 7.2.9-5.3 5 1.4 7.1L12 17.9l-6.4 3.5L7 14.3 1.7 9.3l7.2-.9z" fill="#fbb829"/></symbol>
</svg>
<div class="page">

<header class="site-header abs">
  <div class="brand abs"><span class="brand-dot"></span><span class="brand-name">Bright Harbor Goods</span></div>
  <nav class="top-links abs"><span>HOME</span><span class="sep">|</span><span>ABOUT US</span><span class="sep">|</span><span>CONTACT US</span><span class="sep">|</span><span>BLOG</span></nav>
  <div class="call abs">
    <span class="round"><svg class="ico" width="14" height="14" viewBox="0 0 24 24"><path d="M6.6 10.8a15 15 0 006.6 6.6l2.2-2.2c.3-.3.7-.4 1-.2 1.1.4 2.3.6 3.6.6.6 0 1 .4 1 1V20c0 .6-.4 1-1 1A17 17 0 013 4c0-.6.4-1 1-1h3.5c.6 0 1 .4 1 1 0 1.3.2 2.5.6 3.6.1.3 0 .7-.2 1z" fill="#222"/></svg></span>
    <b>1-800-555-0142</b>
  </div>
  <div class="tools abs">
    <span class="round"><svg class="ico" width="13" height="13" viewBox="0 0 24 24"><circle cx="12" cy="7" r="5" fill="#222"/><path d="M2 22c0-6 4-9 10-9s10 3 10 9z" fill="#222"/></svg></span>
    <span class="round"><svg class="ico" width="13" height="13" viewBox="0 0 24 24"><circle cx="10" cy="10" r="6.5" fill="none" stroke="#222" stroke-width="3"/><path d="M15 15l6 6" stroke="#222" stroke-width="3.5"/></svg></span>
    <span class="round" style="position:relative"><svg class="ico" width="14" height="14" viewBox="0 0 24 24"><path d="M1 3h4l3 11h11l3-8H7" fill="none" stroke="#222" stroke-width="2.6"/><circle cx="9" cy="19" r="2" fill="#222"/><circle cx="18" cy="19" r="2" fill="#222"/></svg><span class="cart-count">0</span></span>
  </div>
</header>

<nav class="main-nav abs"><a>REUSABLE BAGS</a><a>SEED PAPER</a><a>REUSABLE BOTTLES</a><a>LANYARDS</a><a>ECO PROMO ITEMS</a></nav>

<div class="crumbs abs"><span>Home</span><span>»</span><span>Non-Woven Reusable Promo Totes</span></div>

<div class="product-band abs"></div>
<h1 class="product-title abs head">Non-Woven Reusable Promo Totes</h1>

<div class="photo-main abs"><div class="fill" role="img" aria-label="Red and tan non-woven tote bags printed with sample client logos"></div></div>
<div class="thumb abs" style="left:74px"><i role="img" aria-label="Lime green tote" style="background:#6cc63c"></i></div>
<div class="thumb abs" style="left:191px"><i role="img" aria-label="Navy blue tote" style="background:#22216b"></i></div>
<div class="thumb abs" style="left:307px"><i role="img" aria-label="Royal blue tote" style="background:#1e7cc3"></i></div>
<div class="thumb more abs" style="left:424px">+</div>

<div class="sku abs head">SKU: PP2</div>
<div class="rev-link abs">38 Review(s) | Add Review</div>
<div class="stars-lg abs">
  <svg width="23" height="23"><use href="#star"/></svg><svg width="23" height="23"><use href="#star"/></svg><svg width="23" height="23"><use href="#star"/></svg><svg width="23" height="23"><use href="#star"/></svg><svg width="23" height="23"><use href="#star"/></svg>
</div>
<div class="spec-line abs" style="top:438px">Size : 13" W x 14" H x 7" D</div>
<div class="spec-line abs" style="top:485px">Thickness: 100 GSM</div>

<div class="stock-h abs head" style="top:539px">In-Stock</div>
<div class="price-table abs" style="top:592px">
  <div class="lab">Qty</div><div>1</div><div>100+</div><div>250+</div><div>500+</div><div>1,000+</div><div>2,500+</div><div>5,000+</div>
  <div class="lab">Price</div><div>$0.69</div><div>$1.46</div><div>$1.35</div><div>$1.30</div><div>$1.26</div><div>$1.23</div><div>$1.19</div>
</div>

<div class="stock-h abs head" style="top:715px">Overseas</div>
<div class="price-table abs" style="top:769px">
  <div class="lab">Qty</div><div>1</div><div>1,000+</div><div>3,000+</div><div>5,000+</div><div>10,000+</div><div>25,000+</div><div>50,000+</div>
  <div class="lab">Price</div><div>$0.69</div><div>$1.14</div><div>$0.94</div><div>$0.89</div><div>$0.84</div><div>$0.74</div><div>$0.69</div>
</div>

<div class="btn quote abs">Request A Quote</div>
<div class="btn buy abs">Buy Now</div>
<div class="btn sample abs">Order Free Sample</div>

<section class="sample-form abs">
  <h2>COMPLETE THIS FORM &amp; RECEIVE A FREE SAMPLE</h2>
  <div class="field" style="left:286px;top:89px">Name</div>
  <div class="field" style="left:608px;top:89px">Email</div>
  <div class="field" style="left:286px;top:146px">Phone</div>
  <div class="field" style="left:608px;top:146px">--Quantity--<svg class="ico" width="10" height="10" viewBox="0 0 10 10"><path d="M1 3l4 4 4-4" fill="none" stroke="#222" stroke-width="2"/></svg></div>
  <div class="submit">SUBMIT</div>
</section>

<div class="tabs abs"><span class="on">DETAILS</span><span class="sep" style="margin-left:6px">|</span><span>REVIEWS</span><span class="sep">|</span><span>ADDITIONAL INFO</span><span class="sep">|</span><span>SHIPPING ESTIMATOR</span></div>
<h2 class="details-h abs head">NON-WOVEN PROMOTIONAL TOTE BAGS WHOLESALE</h2>

<dl class="specs abs">
  <dt>Name</dt><dd>Non-Woven Reusable Promo Totes</dd>
  <dt>SKU</dt><dd>PP2</dd>
  <dt>Size</dt><dd>13" W x 14" H x 7" D</dd>
  <dt>Thickness</dt><dd>100 GSM</dd>
  <dt>Available Colors</dt><dd>Black, Hunter Green, Kelly Green, Lime Green, Maui Blue, Navy Blue, Purple, Red, Royal Blue, Tan, Teal &amp; Yellow</dd>
  <dt>Imprint Area</dt><dd>8" W x 8" H</dd>
  <dt class="tall">Key Features</dt>
  <dd class="tall"><ul class="features">
    <li>Spacious Main Compartment, 1274 Cubic Inches</li>
    <li>22" Carry Straps</li>
    <li>Made from 100 GSM Non-Woven Polypropylene</li>
    <li>Eco-Friendly and 100% Recyclable</li>
    <li>Removable Hard Bottom Insert at the Base</li>
    <li>5 Day Standard Production / RUSH service available</li>
    <li>10 Day Production for Full Color Artwork</li>
    <li>8" Wide x 8" High Imprint Area</li>
    <li>Made From Recycled Content</li>
  </ul></dd>
</dl>

<section class="reviews abs">
  <h2>CUSTOMER REVIEWS (38)</h2>
  <article class="review" style="left:0;top:96px;width:575px;height:205px;padding-left:162px">
    <div class="stars"><svg width="22" height="22"><use href="#star"/></svg><svg width="22" height="22"><use href="#star"/></svg><svg width="22" height="22"><use href="#star"/></svg><svg width="22" height="22"><use href="#star"/></svg><svg width="22" height="22"><use href="#star"/></svg></div>
    <p style="width:390px">I was able to use this promotional tote bag to promote my business just the way I had planned. Very cost effective and they met my deadline with ease.</p>
    <div class="by">Review by <b>Daniel R</b></div>
  </article>
  <article class="review" style="left:612px;top:163px;width:588px;height:204px;padding-left:36px">
    <div class="stars"><svg width="22" height="22"><use href="#star"/></svg><svg width="22" height="22"><use href="#star"/></svg><svg width="22" height="22"><use href="#star"/></svg><svg width="22" height="22"><use href="#star"/></svg><svg width="22" height="22"><use href="#star"/></svg></div>
    <p style="width:410px">These bags were a big time hit at my annual convention. Our logo really stood out nicely on the center of these eco-friendly bags.&nbsp; The cost fit within our budget.&nbsp; Great company t.... <span class="more">Read more</span></p>
    <div class="by">Review by <b>Karen M</b></div>
  </article>
</section>
<a class="all-link abs">See All 38 Customer Reviews</a>

<h2 class="rec-h abs head">RECOMMENDED PRODUCTS</h2>
<div class="card abs" style="left:74px">
  <div class="pic"><i role="img" aria-label="Green and red promotional totes" style="background:linear-gradient(90deg,#3fc33a,#7a3fb8 45%,#e0262b 55%)"></i></div>
  <div class="info"><b>Size:</b>&nbsp; 16" W x 12" H x 6" D<br><b>As Low As:</b> $0.54<br><b>SKU:</b>&nbsp; PP9</div>
  <div class="stars"><svg width="19" height="19"><use href="#star"/></svg><svg width="19" height="19"><use href="#star"/></svg><svg width="19" height="19"><use href="#star"/></svg><svg width="19" height="19"><use href="#star"/></svg><svg width="19" height="19"><use href="#star"/></svg></div>
  <small>(23 Reviews)</small>
</div>
<div class="card abs" style="left:344px">
  <div class="pic"><i role="img" aria-label="Purple and tan promotional totes" style="background:linear-gradient(90deg,#5b3a8e,#6b4f9c 45%,#e2c8a2 55%)"></i></div>
  <div class="info"><b>Size:</b>&nbsp; 16" W x 12" H x 6" D<br><b>As Low As:</b> $0.54<br><b>SKU:</b>&nbsp; PP9</div>
  <div class="stars"><svg width="19" height="19"><use href="#star"/></svg><svg width="19" height="19"><use href="#star"/></svg><svg width="19" height="19"><use href="#star"/></svg><svg width="19" height="19"><use href="#star"/></svg><svg width="19" height="19"><use href="#star"/></svg></div>
  <small>(23 Reviews)</small>
</div>
<div class="card abs" style="left:615px">
  <div class="pic"><i role="img" aria-label="Blue and red promotional totes" style="background:linear-gradient(90deg,#1d5fa8,#2a72b8 45%,#d72630 55%)"></i></div>
  <div class="info"><b>Size:</b>&nbsp; 16" W x 12" H x 6" D<br><b>As Low As:</b> $0.54<br><b>SKU:</b>&nbsp; PP9</div>
  <div class="stars"><svg width="19" height="19"><use href="#star"/></svg><svg width="19" height="19"><use href="#star"/></svg><svg width="19" height="19"><use href="#star"/></svg><svg width="19" height="19"><use href="#star"/></svg><svg width="19" height="19"><use href="#star"/></svg></div>
  <small>(23 Reviews)</small>
</div>
<div class="card abs" style="left:884px">
  <div class="pic"><i role="img" aria-label="Green and tan promotional totes" style="background:linear-gradient(90deg,#1f9a46,#2aa54e 45%,#d8c39b 55%)"></i></div>
  <div class="info"><b>Size:</b>&nbsp; 16" W x 12" H x 6" D<br><b>As Low As:</b> $0.54<br><b>SKU:</b>&nbsp; PP9</div>
  <div class="stars"><svg width="19" height="19"><use href="#star"/></svg><svg width="19" height="19"><use href="#star"/></svg><svg width="19" height="19"><use href="#star"/></svg><svg width="19" height="19"><use href="#star"/></svg><svg width="19" height="19"><use href="#star"/></svg></div>
  <small>(23 Reviews)</small>
</div>

<footer class="site-footer abs">
  <div class="imprint-card">
    <div class="t">IMPRINT OPTIONS</div>
    <div class="box">
      <div class="r1">In-Stock Production</div>
      <div class="r2">Orders of 288 pcs or more</div>
      <div class="r3">Includes 1 Imprint Color</div>
      <div class="row"><span>Imprint Size:</span><span>4" W x 7" H</span></div>
      <div class="row"><span>Additional Colors 288 pcs:<br>Additional Colors 500+ pcs:</span><span>$0.74 each<br>$0.54 each</span></div>
      <div class="row b"><span>Full Color Imprint 288 pcs:<br>Full Color Imprint 500+ pcs:</span><span>$0.99 each<br>$0.79 each</span></div>
      <div class="row"><span>Set Up Fee:<br>Full Color Set Up Fee:</span><span>$55 per color<br>$95 per color</span></div>
    </div>
  </div>
  <div class="foot-brand">Bright Harbor Goods</div>
  <p class="foot-about">Bright Harbor Goods is an eco-friendly company that specializes in manufacturing custom bags. BHG was founded in 2009 and has strived to make the world a better place ever since.</p>
  <div class="foot-col" style="left:693px">
    <h3>USEFUL LINKS</h3>
    <ul><li>Customer Service</li><li>Our Story</li><li>Site Map</li><li>FTC Disclosure</li><li>Privacy Policy</li><li>Contact Us</li><li>Art &amp; Imprint Policy</li><li>Free Rush</li></ul>
  </div>
  <div class="foot-col" style="left:934px">
    <h3>WHY BUY FROM US</h3>
    <ul><li>Reusable Bag Stats</li><li>Best Price Guarantee</li><li>Return &amp; Refund Policy</li><li>Shipping Policy</li><li>In-Stock &amp; Custom Production</li><li>Frequently Asked Questions</li></ul>
  </div>
</footer>

<section class="contact-band abs">
  <svg class="abs" style="left:74px;top:34px" width="26" height="34" viewBox="0 0 24 32"><path d="M12 0C5.4 0 0 5.2 0 11.7 0 20 12 32 12 32s12-12 12-20.3C24 5.2 18.6 0 12 0z" fill="#fff"/><circle cx="12" cy="11.5" r="4.5" fill="#33b5b2"/></svg>
  <div class="addr">450 Harbor Lane, Suite 8<br>Port Avery, FL 33000</div>
  <svg class="abs" style="left:491px;top:37px" width="26" height="26" viewBox="0 0 24 24"><path d="M6.6 10.8a15 15 0 006.6 6.6l2.2-2.2c.3-.3.7-.4 1-.2 1.1.4 2.3.6 3.6.6.6 0 1 .4 1 1V20c0 .6-.4 1-1 1A17 17 0 013 4c0-.6.4-1 1-1h3.5c.6 0 1 .4 1 1 0 1.3.2 2.5.6 3.6.1.3 0 .7-.2 1z" fill="#fff"/></svg>
  <div class="ph">1-800-555-0142</div>
  <svg class="abs" style="left:864px;top:38px" width="26" height="20" viewBox="0 0 26 20"><rect x="1.5" y="1.5" width="23" height="17" rx="2" fill="none" stroke="#fff" stroke-width="2.5"/><path d="M2 3l11 8 11-8" fill="none" stroke="#fff" stroke-width="2.5"/></svg>
  <div class="em">hello@brightharborgoods-example.com</div>
</section>

<div class="bottom-bar abs">
  <div class="copy">© 2020 &nbsp;|&nbsp; www.brightharborgoods-example.com</div>
  <div class="social"><i></i><i></i><i></i><i></i><i></i></div>
  <div class="code">M1</div>
</div>

</div>
</body>
</html>
```